Sports / Entertainment Media Co needs a biz card design

We are a media co / luxury lifestyle brand that targets professional athletes, entertainers and high net-worth fans. We are currently preparing for a relaunch and in need for new biz cards. I envision a black on black card with a pop of color on opposite side. Color Palette black, white, red etc. I want this card to exude sexiness and power. Very high stylized, hip and cool. I have attached the logo - I would like to see it all in black, but also open to other ideas. I will also upload a current card with all information needed on this new card. Furthermore I will add some samples of other cards I love. Thanks!!!
Updates

I provided suggestions, however I am open to all ideas!!   Be as creative as you can.  Think cutting-edge, sexy and powerful.  Take a look at the cards I uploaded to get a sense for what I like.  Thanks!!!

Industry/Entity Type

Entertainment

```html
<!DOCTYPE html>
<html lang="en">
<head>
<meta charset="utf-8">
<title>Glide Media Ventures – Business Card</title>
<link rel="stylesheet" href="https://fonts.googleapis.com/css2?family=Josefin+Sans:wght@300;400;600&display=swap">
<style>
  :root {
    --backdrop: #3b3b3d;
    --card: #2e2e30;
    --card-edge: #262628;
    --ink-dark: #1b1a1c;
    --ink-light: #d9d9d9;
    --ink-muted: #8f8f92;
    --accent-red: #e0232a;
  }
  * { margin: 0; padding: 0; box-sizing: border-box; }
  html, body {
    width: 1200px;
    height: 914px;
    overflow: hidden;
    background: var(--backdrop);
    font-family: "Josefin Sans", sans-serif;
  }
  .stage {
    position: relative;
    width: 1200px;
    height: 914px;
  }
  .card {
    position: absolute;
    background: var(--card);
    border-radius: 26px;
    box-shadow: 0 18px 40px rgba(0,0,0,0.35), inset 0 0 0 1px var(--card-edge);
    overflow: hidden;
  }

  /* Back of card: wordmark side */
  .card--back {
    left: 90px;
    top: 287px;
    width: 592px;
    height: 340px;
  }
  .back__wordmark {
    position: absolute;
    left: 40px;
    top: 78px;
    font-size: 190px;
    font-weight: 400;
    line-height: 1;
    letter-spacing: -4px;
    color: var(--ink-dark);
  }
  .back__web {
    position: absolute;
    left: 46px;
    bottom: 44px;
    font-size: 20px;
    font-weight: 600;
    color: var(--ink-muted);
    letter-spacing: 0.5px;
  }

  /* Front of card: contact side */
  .card--front {
    left: 770px;
    top: 197px;
    width: 340px;
    height: 520px;
  }
  .front__name {
    position: absolute;
    left: 44px;
    top: 70px;
    font-size: 19px;
    font-weight: 400;
    letter-spacing: 1.5px;
    text-transform: uppercase;
  }
  .front__first { color: var(--accent-red); }
  .front__last { color: var(--ink-dark); }
  .front__title {
    position: absolute;
    left: 44px;
    top: 98px;
    font-size: 11px;
    font-weight: 300;
    letter-spacing: 1.6px;
    color: var(--ink-light);
    text-transform: uppercase;
  }
  .front__address {
    position: absolute;
    left: 90px;
    top: 160px;
    font-size: 11px;
    font-weight: 300;
    line-height: 1.55;
    letter-spacing: 0.8px;
    color: var(--ink-light);
    text-transform: uppercase;
  }
  .front__contacts {
    position: absolute;
    left: 60px;
    top: 222px;
    list-style: none;
    font-size: 11px;
    font-weight: 300;
    letter-spacing: 0.8px;
    color: var(--ink-light);
  }
  .front__contacts li {
    display: flex;
    line-height: 2.1;
  }
  .contact__label {
    width: 28px;
    font-weight: 400;
  }
  .front__accent {
    position: absolute;
    left: 0;
    bottom: 0;
  }
</style>
</head>
<body>
  <main class="stage">
    <section class="card card--back" aria-label="Business card back">
      <div class="back__wordmark">glide</div>
      <div class="back__web">glidemag.com</div>
    </section>

    <section class="card card--front" aria-label="Business card front">
      <p class="front__name"><span class="front__first">Dana</span> <span class="front__last">Morrow</span></p>
      <p class="front__title">| Pres | Glide Media Ventures LLC</p>
      <p class="front__address">2140 NE 41st Street,<br>Ste 300, Miami, FL 33160</p>
      <ul class="front__contacts">
        <li><span class="contact__label">T</span>305.555.0142</li>
        <li><span class="contact__label">M</span>954.555.0187</li>
        <li><span class="contact__label">F</span>305.555.0163</li>
        <li><span class="contact__label">E</span>dana@glidemag.com</li>
      </ul>
      <svg class="front__accent" width="340" height="120" viewBox="0 0 340 120" aria-hidden="true">
        <rect x="44" y="40" width="70" height="6" fill="var(--accent-red)"/>
        <rect x="44" y="54" width="150" height="2" fill="var(--ink-dark)"/>
      </svg>
    </section>
  </main>
</body>
</html>
```